Landing Page & Email Signature

I am looking for a new landing page as well as an email signature to align with the change in business. I have included the new logo/emblem which I'd like incorporated into the design and the current landing page is www.delmorquivex.com.au should you wish to see the old version.

```html
<!DOCTYPE html>
<html lang="en">
<head>
<meta charset="utf-8">
<title>Delmor Quivex – Transport &amp; Logistics</title>
<link rel="stylesheet" href="https://fonts.googleapis.com/css2?family=Russo+One&family=Roboto:wght@400;500;700&display=swap">
<style>
:root{
  --red:#c8102e;
  --red-dark:#9e0c22;
  --ink:#222;
  --grey:#666;
  --light:#f4f4f4;
  --footer:#1b1b1b;
  --white:#fff;
}
*{box-sizing:border-box;margin:0;padding:0}
html,body{width:1200px;height:2188px;overflow:hidden;background:var(--white)}
body{position:relative;font-family:'Roboto',sans-serif;color:var(--ink)}
.abs{position:absolute}

/* header */
.site-header{position:absolute;left:0;top:0;width:1200px;height:124px;background:var(--white)}
.brand{left:40px;top:22px;display:flex;align-items:center;gap:12px}
.brand-dot{width:22px;height:22px;border-radius:50%;background:var(--red)}
.brand-name{font-family:'Russo One',sans-serif;font-size:30px;color:var(--red);line-height:1}
.brand-url{left:74px;top:62px;font-size:12px;color:var(--grey)}
.social{left:694px;top:30px;display:flex;gap:8px;align-items:center}
.social span{width:26px;height:26px;border-radius:50%;background:var(--red);display:block}
.social span:nth-child(1){background:#3b5998}
.social span:nth-child(2){background:#1da1f2}
.lang{left:824px;top:36px;font-size:12px;color:var(--grey);display:flex;gap:6px;align-items:center}
.lang i{width:18px;height:12px;background:#2b4aa0;display:block}
.main-nav{left:362px;top:80px;display:flex;gap:28px;font-size:15px;font-weight:700;text-transform:uppercase}
.main-nav a{color:var(--ink);text-decoration:none}
.main-nav a.active{color:var(--red)}
.call-box{left:910px;top:0;width:290px;height:124px;background:var(--red);clip-path:polygon(40px 0,100% 0,100% 100%,0 100%);color:var(--white);padding:44px 0 0 100px}
.call-box small{display:block;font-size:15px}
.call-box strong{display:block;font-size:24px;font-weight:700;margin-top:2px}

/* hero */
.hero{left:0;top:124px;width:1200px;height:646px;background:linear-gradient(135deg,#9fb3c4 0%,#6c7f92 35%,#3a3438 60%,#7a3a2a 80%,#2a2528 100%)}
.hero-panel{left:556px;top:230px;width:604px;height:380px;background:rgba(0,0,0,.78);padding:50px 40px}
.hero-panel h1{font-family:'Russo One',sans-serif;font-weight:400;color:var(--white);font-size:40px;line-height:48px;text-transform:uppercase}
.hero-btn{display:inline-block;margin-top:30px;border:2px solid var(--red);color:var(--white);font-size:12px;padding:8px 22px;border-radius:20px;text-transform:uppercase}
.hero-arrows{left:680px;top:670px;display:flex;gap:14px}
.hero-arrows span{width:34px;height:34px;border-radius:50%;background:#444;color:#fff;display:flex;align-items:center;justify-content:center;font-size:16px}
.hero-arrows span+span{background:var(--red)}

/* process */
.section-title{font-family:'Russo One',sans-serif;font-weight:400;font-size:48px;text-transform:uppercase;color:var(--red);text-align:center}
.process-title{left:0;top:818px;width:1200px}
.process-intro{left:330px;top:904px;width:540px;text-align:center;font-size:13px;line-height:20px;color:var(--grey)}
.step{width:200px;text-align:center}
.step-icon{width:96px;height:96px;margin:0 auto;border-radius:50%;background:var(--white);box-shadow:0 4px 14px rgba(0,0,0,.12);border-left:5px solid var(--red);display:flex;align-items:center;justify-content:center}
.step-label{font-size:18px;font-weight:500;margin-top:14px}

/* contact */
.contact{left:0;top:1290px;width:1200px;height:500px;background:linear-gradient(160deg,var(--red) 0%,var(--red-dark) 100%);clip-path:polygon(110px 0,1090px 0,1200px 90px,1200px 100%,0 100%,0 90px)}
.contact-title{left:0;top:1356px;width:1200px;color:var(--white)}
.field{background:var(--white);border-radius:3px;font-size:13px;color:var(--grey);padding:12px 14px}
.submit{left:528px;top:1670px;width:144px;height:40px;border:2px solid var(--white);border-radius:22px;color:var(--white);font-weight:700;font-size:14px;display:flex;align-items:center;justify-content:center}

/* footer */
.site-footer{left:0;top:1790px;width:1200px;height:398px;background:var(--footer);color:#ccc}
.info{width:280px;text-align:center}
.info-icon{width:72px;height:72px;margin:0 auto;border-radius:50%;background:var(--white);display:flex;align-items:center;justify-content:center}
.info h3{color:var(--red);font-size:18px;font-weight:500;margin-top:18px}
.info p{font-size:13px;line-height:19px;margin-top:8px}
.divider{width:1px;height:180px;background:#444}
.footer-rule{left:240px;top:2090px;width:720px;height:1px;background:#444}
.copyright{left:0;top:2110px;width:1200px;text-align:center;font-size:13px}
</style>
</head>
<body>

<header class="site-header">
  <div class="abs brand"><span class="brand-dot"></span><span class="brand-name">DELMOR QUIVEX</span></div>
  <div class="abs brand-url">www.delmorquivex.com.au</div>
  <div class="abs social"><span></span><span></span><span></span></div>
  <div class="abs lang">Eng <i></i></div>
  <nav class="abs main-nav">
    <a class="active" href="#">Home</a><a href="#">About</a><a href="#">Services</a><a href="#">Blog</a><a href="#">Testimonials</a><a href="#">Contact us</a>
  </nav>
  <div class="abs call-box"><small>Call us Today :</small><strong>+1 555 014 2290</strong></div>
</header>

<section class="abs hero" role="img" aria-label="Cargo plane taking off over a highway with a truck and a container port at dusk"></section>
<div class="abs hero-panel">
  <h1>We look forward to satisfy your current and future needs!</h1>
  <span class="hero-btn">Learn More</span>
</div>
<div class="abs hero-arrows"><span>&#8249;</span><span>&#8250;</span></div>

<h2 class="abs section-title process-title">Our Process</h2>
<p class="abs process-intro">Lorem ipsum dolor sit amet, consectetur adipiscing elit, sed do eiusmod tempor incididunt ut labore tempor incididunt ut labore et dolore magna aliqua et dolore magna aliqua.</p>

<svg class="abs" style="left:0;top:990px" width="1200" height="200" aria-hidden="true">
  <g fill="none" stroke="#bbb" stroke-width="2" stroke-dasharray="5 6">
    <path d="M325 60 Q380 130 420 110"/>
    <path d="M560 110 Q600 40 640 60"/>
    <path d="M780 60 Q830 130 880 110"/>
  </g>
</svg>

<div class="abs step" style="left:160px;top:1000px">
  <div class="step-icon"><svg width="44" height="30"><rect x="2" y="2" width="40" height="26" rx="3" fill="none" stroke="#222" stroke-width="3"/><circle cx="22" cy="15" r="6" fill="none" stroke="#222" stroke-width="3"/></svg></div>
  <div class="step-label">Taking Order</div>
</div>
<div class="abs step" style="left:390px;top:1040px">
  <div class="step-icon"><svg width="44" height="40"><rect x="4" y="16" width="20" height="20" fill="none" stroke="#222" stroke-width="3"/><path d="M28 10h12M34 4l6 6-6 6" fill="none" stroke="#222" stroke-width="3"/></svg></div>
  <div class="step-label">Sent Shipment</div>
</div>
<div class="abs step" style="left:630px;top:1000px">
  <div class="step-icon"><svg width="40" height="40"><rect x="4" y="14" width="32" height="22" fill="none" stroke="#222" stroke-width="3"/><rect x="2" y="8" width="36" height="8" fill="none" stroke="#222" stroke-width="3"/><path d="M20 8v28" stroke="#222" stroke-width="3"/></svg></div>
  <div class="step-label">Get the Cargo</div>
</div>
<div class="abs step" style="left:870px;top:1040px">
  <div class="step-icon"><svg width="40" height="40"><path d="M4 20 20 5 36 20M9 17v19h22V17" fill="none" stroke="#222" stroke-width="3"/><rect x="16" y="24" width="8" height="12" fill="#222"/></svg></div>
  <div class="step-label">Delivered to door</div>
</div>

<section class="abs contact"></section>
<h2 class="abs section-title contact-title">Contact Us</h2>
<div class="abs field" style="left:236px;top:1442px;width:236px;height:42px">Name</div>
<div class="abs field" style="left:484px;top:1442px;width:236px;height:42px">Email address</div>
<div class="abs field" style="left:732px;top:1442px;width:232px;height:42px">Phone</div>
<div class="abs field" style="left:236px;top:1506px;width:728px;height:140px">Message</div>
<div class="abs submit">SUBMIT</div>

<footer class="abs site-footer"></footer>
<div class="abs info" style="left:130px;top:1850px">
  <div class="info-icon"><svg width="26" height="34"><path d="M13 32C13 32 2 19 2 12a11 11 0 0 1 22 0c0 7-11 20-11 20z" fill="#c8102e"/><circle cx="13" cy="12" r="4" fill="#fff"/></svg></div>
  <h3>Address</h3>
  <p>123 Lorem ipsum dolor sit amet,<br>consectetur adipiscing</p>
</div>
<div class="abs divider" style="left:430px;top:1850px"></div>
<div class="abs info" style="left:460px;top:1850px">
  <div class="info-icon"><svg width="30" height="30"><path d="M6 2l6 1 2 7-4 3c2 4 4 6 8 8l3-4 7 2 1 6c-1 2-3 3-5 3C12 27 3 18 2 7c0-2 2-4 4-5z" fill="#222"/></svg></div>
  <h3>Phone</h3>
  <p>+1 555 014 7731</p>
</div>
<div class="abs divider" style="left:770px;top:1850px"></div>
<div class="abs info" style="left:790px;top:1850px">
  <div class="info-icon"><svg width="32" height="24"><rect x="1" y="1" width="30" height="22" rx="2" fill="#222"/><path d="M2 3l14 11L30 3" fill="none" stroke="#fff" stroke-width="2"/></svg></div>
  <h3>Email</h3>
  <p>hello@delmorquivex.com.au</p>
</div>
<div class="abs footer-rule"></div>
<p class="abs copyright">© 2022 Company name &nbsp;|&nbsp; All Rights Reserved &nbsp;|&nbsp; Terms and Conditions</p>

</body>
</html>
```